Beautify our counselling web application

I have a web application in development and at the moment it is very plain.
It has being developed with laravel and vue. I need a simple design for the user interface to make it look more sleek and professional. I will need someone who is able to code the design as part of the service. The app is very low-cost for voluntary and social enterprise services and we don't have a lot of money so I need someone who is just starting out or someone with a big heart.
I have uploaded current pages to show the contents.
I will tip for good work.

Target Market(s)

Counsellors and psychotherapists

Industry/Entity Type

SaaS

Font styles to use
Serif
Sans Serif

Colors
0054AA
0677BA
7BADD7
CADEEF
E8F1F8

Requirements
Must have
• Ability to code the design into the current site
Nice to have
• elegant, modern. cool, profession. nice examples include merovaultix.com quillbanter.com fenrodu.com
Should not have
• corny literal 90s icons, icons with more than one colour using primary colours

```html
<!DOCTYPE html>
<html lang="en">
<head>
<meta charset="utf-8">
<title>Tendwell – Interface Screens</title>
<link href="https://fonts.googleapis.com/css2?family=Nunito+Sans:wght@300;400;600;800&display=swap" rel="stylesheet">
<style>
:root{
  --primary:#0054AA;
  --secondary:#0677BA;
  --soft:#7BADD7;
  --pale:#CADEEF;
  --mist:#E8F1F8;
  --row:#F6F9FC;
  --ink:#1b1b1b;
  --text:#3a3a3a;
  --stage:#212121;
  --white:#ffffff;
}
*{box-sizing:border-box;margin:0;padding:0}
html,body{width:762px;height:1200px;overflow:hidden;background:var(--stage)}
body{position:relative;font-family:"Nunito Sans",sans-serif;color:var(--text)}
.screen{position:absolute;left:60px;width:648px;height:324px;background:var(--white);overflow:hidden}
.screen--caseload{top:77px}
.screen--client{top:438px}
.screen--dashboard{top:796px}

.sidebar{position:absolute;left:0;top:0;width:104px;height:100%;background:var(--white);box-shadow:1px 0 3px rgba(0,0,0,.05);z-index:2}
.brand{position:absolute;left:17px;top:9px;font-weight:800;font-size:9.5px;color:var(--primary)}
.nav{position:absolute;left:0;top:36px;width:104px;list-style:none}
.nav li{height:17px;margin-bottom:4px;display:flex;align-items:center;padding-left:10px;font-size:6px;color:var(--ink)}
.nav li svg{width:6.5px;height:6.5px;margin-right:6px;stroke:#333;fill:none;stroke-width:1.2}
.nav li.is-active{background:var(--mist)}

.topbar{position:absolute;left:104px;top:0;right:0;height:28px;background:var(--mist)}
.topbar .tool{position:absolute;top:7px;width:14px;height:14px;stroke:var(--primary);fill:none;stroke-width:1.6}
symbol path{fill:none}

.page-title{position:absolute;font-size:9px;font-weight:600;color:var(--ink)}

.search{position:absolute;left:495px;top:40px;width:95px;height:15px;border:1px solid #d3d3d3;font-size:5px;padding:4px 6px;color:#555}
.search svg{position:absolute;right:5px;top:4px;width:5px;height:5px;stroke:#333;fill:none;stroke-width:1.6}
.filter{position:absolute;left:596px;top:40px;width:41px;height:15px;border:1px solid #d3d3d3;font-size:5px;padding:4px 6px;color:#555}
.filter svg{position:absolute;right:5px;top:5px;width:5px;height:4px;stroke:#333;fill:none;stroke-width:1.4}
.caseload-table{position:absolute;left:121px;top:64px;width:516px;border-collapse:collapse;table-layout:fixed;font-size:5.8px}
.caseload-table th{background:var(--secondary);color:var(--white);font-weight:400;height:18.5px;text-align:left}
.caseload-table td{height:27.5px;color:#444;font-weight:300}
.caseload-table tbody tr:nth-child(even) td{background:var(--row)}
.caseload-table th:first-child,.caseload-table td:first-child{padding-left:11px}
.risk-dot{display:inline-block;width:6px;height:6px;border-radius:50%;background:var(--secondary)}
.contact-total{display:inline-block;background:var(--soft);color:var(--white);font-size:5.6px;width:32px;height:13px;line-height:13px;text-align:center}

.tab-btn{position:absolute;top:44px;height:14px;background:var(--primary);color:var(--white);font-size:5.6px;display:flex;align-items:center;justify-content:center;white-space:nowrap}
.episode{position:absolute;left:119px;top:75px;width:520px;height:91px;background:var(--mist)}
.episode-title{position:absolute;left:13px;top:8px;font-size:7.5px;color:var(--secondary)}
.episode-start{position:absolute;left:368px;top:9px;font-size:6.2px;color:var(--ink);display:flex;align-items:center}
.episode-start svg{width:8px;height:5px;margin-left:5px;stroke:#333;fill:none;stroke-width:1.3}
.end-btn{position:absolute;left:472px;top:7px;width:40px;height:12px;background:var(--primary);color:var(--white);font-size:5px;display:flex;align-items:center;justify-content:center}
.record-tile{position:absolute;width:79px;height:20px;background:var(--white);font-size:6.2px;font-weight:300;color:#333;display:flex;align-items:center;justify-content:center}

.welcome{position:absolute;left:127px;top:69px;font-size:9px;font-weight:600;color:var(--ink)}
.panel{position:absolute;left:129px;width:508px;border:1px solid var(--primary);background:var(--white)}
.panel-head{height:19px;background:var(--primary);color:var(--white);font-size:6.5px;font-weight:600;padding-left:8px;display:flex;align-items:center}
.panel-body{display:flex;align-items:center;justify-content:center;font-size:8.5px;font-weight:300;color:#333}
.create-btn{position:absolute;right:3px;top:3px;width:68px;height:13px;background:var(--white);color:var(--primary);font-size:6px;font-weight:600;display:flex;align-items:center;justify-content:center}
</style>
</head>
<body>

<svg width="0" height="0" style="position:absolute" aria-hidden="true">
  <symbol id="i-home" viewBox="0 0 12 12"><path d="M1.5 6 6 1.8 10.5 6M3 5v5.2h6V5"/></symbol>
  <symbol id="i-edit" viewBox="0 0 12 12"><path d="M6 2H2v8h8V6M5 7l.4-1.6L9.8 1l1.2 1.2L6.6 6.6z"/></symbol>
  <symbol id="i-cal" viewBox="0 0 12 12"><path d="M1.5 2.5h9v8h-9zM1.5 5h9M4 1v2.5M8 1v2.5"/></symbol>
  <symbol id="i-book" viewBox="0 0 12 12"><path d="M2 1h8v10H2zM6 3.6a1.2 1.2 0 1 0 0 .1M4 8.5c.4-1.4 3.6-1.4 4 0"/></symbol>
  <symbol id="i-users" viewBox="0 0 12 12"><path d="M4 4.5a1.4 1.4 0 1 0 0 .1M8 4.5a1.4 1.4 0 1 0 0 .1M1 10c.5-2.6 5.5-2.6 6 0M5 10c.5-2.6 5.5-2.6 6 0"/></symbol>
  <symbol id="i-cog" viewBox="0 0 12 12"><path d="M6 4.3a1.7 1.7 0 1 0 0 .1M6 1v1.5M6 9.5V11M1 6h1.5M9.5 6H11M2.5 2.5l1 1M8.5 8.5l1 1M2.5 9.5l1-1M8.5 3.5l1-1"/></symbol>
  <symbol id="i-user" viewBox="0 0 12 12"><path d="M6 3.2a1.8 1.8 0 1 0 0 .1M2.5 10.5c.6-3.4 6.4-3.4 7 0"/></symbol>
  <symbol id="i-clip" viewBox="0 0 12 12"><path d="M2.5 2h7v9.5h-7zM4.5 1h3v2h-3zM4.3 7l1.3 1.3 2.3-2.6"/></symbol>
  <symbol id="i-mon" viewBox="0 0 12 12"><path d="M6 1.5a4.5 4.5 0 1 0 .1 0M6 4a2 2 0 1 0 .1 0M6 6l3 3"/></symbol>
  <symbol id="i-tpl" viewBox="0 0 12 12"><path d="M1.5 1.5h4v4h-4zM6.5 1.5h4v2h-4zM6.5 4.5h4v6h-4zM1.5 6.5h4v4h-4z"/></symbol>
  <symbol id="t-out" viewBox="0 0 24 24"><path d="M13 3H4v18h9M9 12h12M17 8l4 4-4 4"/></symbol>
  <symbol id="t-help" viewBox="0 0 24 24"><path d="M12 2a10 10 0 1 0 .1 0M9.3 9.2a2.8 2.8 0 1 1 3.9 2.6c-.8.4-1.2 1-1.2 1.9v.8M12 17v.6"/></symbol>
  <symbol id="t-user" viewBox="0 0 24 24"><path d="M12 3a4.5 4.5 0 1 0 .1 0M4 22c1-6.5 15-6.5 16 0"/></symbol>
</svg>

<section class="screen screen--caseload">
  <aside class="sidebar">
    <div class="brand">Tendwell</div>
    <ul class="nav">
      <li><svg><use href="#i-home"/></svg>Dashboard</li>
      <li class="is-active"><svg><use href="#i-edit"/></svg>Caseload</li>
      <li><svg><use href="#i-cal"/></svg>Calendar</li>
      <li><svg><use href="#i-book"/></svg>Address Book</li>
      <li><svg><use href="#i-users"/></svg>Users</li>
      <li><svg><use href="#i-cog"/></svg>Services</li>
      <li><svg><use href="#i-user"/></svg>Clients</li>
      <li><svg><use href="#i-clip"/></svg>Audit</li>
      <li><svg><use href="#i-mon"/></svg>Monitoring</li>
      <li><svg><use href="#i-tpl"/></svg>Templates</li>
    </ul>
  </aside>
  <header class="topbar">
    <svg class="tool" style="left:477px"><use href="#t-out"/></svg>
    <svg class="tool" style="left:498px"><use href="#t-help"/></svg>
    <svg class="tool" style="left:522px"><use href="#t-user"/></svg>
  </header>
  <h1 class="page-title" style="left:122px;top:41px">Caseload</h1>
  <div class="search">Search<svg viewBox="0 0 10 10"><path d="M4 1a3 3 0 1 0 .1 0M6.2 6.2 9 9"/></svg></div>
  <div class="filter">Filter<svg viewBox="0 0 10 6"><path d="M1 1l4 4 4-4"/></svg></div>
  <table class="caseload-table">
    <colgroup><col style="width:37px"><col style="width:38px"><col style="width:77px"><col style="width:37px"><col style="width:62px"><col style="width:46px"><col style="width:60px"><col style="width:56px"><col style="width:63px"><col style="width:40px"></colgroup>
    <thead><tr><th>Risk</th><th>Alerts</th><th>Client</th><th>ID</th><th>Service</th><th>Therapist</th><th>Date of referral</th><th>First Contact</th><th>Previous Episode</th><th>Contacts</th></tr></thead>
    <tbody>
      <tr><td><span class="risk-dot"></span></td><td></td><td>Colin Marsh</td><td>002</td><td>Demo Service 1</td><td>&nbsp;Owen</td><td>&nbsp;05/07/2022</td><td>23/08/2022</td><td></td><td><span class="contact-total">Total : 3</span></td></tr>
      <tr><td><span class="risk-dot"></span></td><td></td><td>Derek Pennell</td><td>003</td><td>Demo Service 1</td><td>&nbsp;Owen</td><td>&nbsp;13/07/2022</td><td>20/09/2022</td><td></td><td><span class="contact-total">Total : 2</span></td></tr>
      <tr><td><span class="risk-dot"></span></td><td></td><td>Lydia Crane</td><td>004</td><td>Demo Service 1</td><td>&nbsp;Ravi</td><td>&nbsp;19/08/2022</td><td>20/09/2022</td><td>&nbsp;20/09/2022</td><td><span class="contact-total">Total : 3</span></td></tr>
      <tr><td><span class="risk-dot"></span></td><td></td><td>Tessa Holt</td><td>005</td><td>Demo Service 1</td><td>&nbsp;Owen</td><td>&nbsp;17/07/2022</td><td>20/09/2022</td><td></td><td><span class="contact-total">Total : 3</span></td></tr>
      <tr><td><span class="risk-dot"></span></td><td></td><td>Maren Ellis</td><td>006</td><td>Demo Service 1</td><td>&nbsp;Ravi</td><td>&nbsp;23/08/2022</td><td>20/09/2022</td><td></td><td><span class="contact-total">Total : 3</span></td></tr>
      <tr><td><span class="risk-dot"></span></td><td></td><td>Nadia Whitcombe</td><td>007</td><td>Demo Service 1</td><td>&nbsp;Ravi</td><td>&nbsp;23/08/2022</td><td>20/09/2022</td><td></td><td><span class="contact-total">Total : 3</span></td></tr>
      <tr><td><span class="risk-dot"></span></td><td></td><td>Tessa Holt</td><td>008</td><td>Demo Service 1</td><td>&nbsp;Ravi</td><td>&nbsp;23/08/2022</td><td>20/09/2022</td><td></td><td><span class="contact-total">Total : 0</span></td></tr>
      <tr><td><span class="risk-dot"></span></td><td></td><td>Maren Ellis</td><td>009</td><td>Demo Service 1</td><td>&nbsp;Ravi</td><td>&nbsp;23/08/2022</td><td>20/09/2022</td><td></td><td><span class="contact-total">Total : 2</span></td></tr>
    </tbody>
  </table>
</section>

<section class="screen screen--client">
  <aside class="sidebar">
    <div class="brand">Tendwell</div>
    <ul class="nav">
      <li><svg><use href="#i-home"/></svg>Dashboard</li>
      <li class="is-active"><svg><use href="#i-edit"/></svg>Caseload</li>
      <li><svg><use href="#i-cal"/></svg>Calendar</li>
      <li><svg><use href="#i-book"/></svg>Address Book</li>
      <li><svg><use href="#i-users"/></svg>Users</li>
      <li><svg><use href="#i-cog"/></svg>Services</li>
      <li><svg><use href="#i-user"/></svg>Clients</li>
      <li><svg><use href="#i-clip"/></svg>Audit</li>
      <li><svg><use href="#i-mon"/></svg>Monitoring</li>
      <li><svg><use href="#i-tpl"/></svg>Templates</li>
    </ul>
  </aside>
  <header class="topbar">
    <svg class="tool" style="left:477px"><use href="#t-out"/></svg>
    <svg class="tool" style="left:498px"><use href="#t-help"/></svg>
    <svg class="tool" style="left:522px"><use href="#t-user"/></svg>
  </header>
  <h1 class="page-title" style="left:119px;top:44px">Caseload / Colin marsh</h1>
  <div class="tab-btn" style="left:388px;width:42px">Workspace</div>
  <div class="tab-btn" style="left:434px;width:59px">Client Information</div>
  <div class="tab-btn" style="left:499px;width:48px">Client Record</div>
  <div class="tab-btn" style="left:551px;width:48px">Client Progress</div>
  <div class="tab-btn" style="left:603px;width:35px">Payments</div>
  <div class="episode">
    <div class="episode-title">Episode 1</div>
    <div class="episode-start">Started Wed Sep 14, 2022<svg viewBox="0 0 10 6"><path d="M1 5l4-4 4 4"/></svg></div>
    <div class="end-btn">End Episode</div>
    <div class="record-tile" style="left:13px;top:33px">Session Record</div>
    <div class="record-tile" style="left:98px;top:33px">Assessment</div>
    <div class="record-tile" style="left:182px;top:33px">Risk Management</div>
    <div class="record-tile" style="left:266px;top:33px">Treatment Plan</div>
    <div class="record-tile" style="left:351px;top:33px">Safeguarding</div>
    <div class="record-tile" style="left:435px;top:33px">Consent</div>
    <div class="record-tile" style="left:13px;top:57px">Questionnaire</div>
    <div class="record-tile" style="left:98px;top:57px">Document</div>
    <div class="record-tile" style="left:182px;top:57px">Non-Clinical note</div>
    <div class="record-tile" style="left:266px;top:57px">Summart</div>
    <div class="record-tile" style="left:351px;top:57px">Timeline</div>
  </div>
</section>

<section class="screen screen--dashboard">
  <aside class="sidebar">
    <div class="brand">Tendwell</div>
    <ul class="nav">
      <li class="is-active"><svg><use href="#i-home"/></svg>Dashboard</li>
      <li><svg><use href="#i-edit"/></svg>Caseload</li>
      <li><svg><use href="#i-cal"/></svg>Calendar</li>
      <li><svg><use href="#i-book"/></svg>Address Book</li>
      <li><svg><use href="#i-users"/></svg>Users</li>
      <li><svg><use href="#i-cog"/></svg>Services</li>
      <li><svg><use href="#i-user"/></svg>Clients</li>
      <li><svg><use href="#i-clip"/></svg>Audit</li>
      <li><svg><use href="#i-mon"/></svg>Monitoring</li>
      <li><svg><use href="#i-tpl"/></svg>Templates</li>
    </ul>
  </aside>
  <header class="topbar">
    <svg class="tool" style="left:477px"><use href="#t-out"/></svg>
    <svg class="tool" style="left:498px"><use href="#t-help"/></svg>
    <svg class="tool" style="left:522px"><use href="#t-user"/></svg>
  </header>
  <h1 class="page-title" style="left:127px;top:42px">Dashboard</h1>
  <h2 class="welcome">Welcome to Demo</h2>
  <div class="panel" style="top:91px;height:68px">
    <div class="panel-head">Notifications</div>
    <div class="create-btn">Create Notification</div>
    <div class="panel-body" style="height:47px">No Notifications</div>
  </div>
  <div class="panel" style="top:167px;height:68px">
    <div class="panel-head">Today</div>
    <div class="panel-body" style="height:47px">No Appointments!</div>
  </div>
  <div class="panel" style="top:242px;height:68px">
    <div class="panel-head">Reviews</div>
    <div class="panel-body" style="height:47px">No Reviews!</div>
  </div>
</section>

</body>
</html>
```